Business Cards for a law firm

Business cards for our law firm. Use our silhoette logo and OAK PARTNERS - check our website (www.oakpartners.example)

Contact Information for Business Card

our silhouette logo, OAK PARTNERS, 800-555-0147, Dorian Pemberton, dorian@oakpartners.example

Requirements
Must have
• our silhouette logo, OAK PARTNERS, 800-555-0147, Dorian Pemberton, dorian@oakpartners.example

```html
<!DOCTYPE html>
<html lang="en">
<head>
<meta charset="utf-8">
<title>Oak Partners – Business Cards</title>
<link rel="stylesheet" href="https://fonts.googleapis.com/css2?family=Montserrat:wght@400;600;700&display=swap">
<style>
  :root {
    --backdrop: #3a3a3c;
    --paper: #ffffff;
    --navy: #1b3270;
    --ink: #1e1e1e;
    --muted: #6a6a6a;
    --rule: #b8b8b8;
  }
  * { box-sizing: border-box; margin: 0; padding: 0; }
  html, body { width: 1200px; height: 1200px; overflow: hidden; }
  body {
    background: var(--backdrop);
    font-family: "Montserrat", sans-serif;
    position: relative;
  }
  .card {
    position: absolute;
    left: 150px;
    width: 900px;
    height: 514px;
    border-radius: 44px;
    overflow: hidden;
  }
  .card--front { top: 60px; background: var(--paper); }
  .card--back { top: 626px; background: var(--navy); }

  .brand {
    position: absolute;
    display: flex;
    align-items: flex-end;
    gap: 22px;
  }
  .brand__mark {
    width: 70px; height: 70px;
    background: currentColor;
  }
  .brand__name {
    font-weight: 400;
    letter-spacing: 2px;
    line-height: 0.9;
    text-transform: uppercase;
  }
  .card--front .brand { left: 200px; top: 110px; color: var(--navy); }
  .card--front .brand__name { font-size: 62px; }
  .card--back .brand { left: 210px; top: 170px; color: var(--paper); }
  .card--back .brand__name { font-size: 72px; }

  .holder {
    position: absolute;
    left: 70px;
    top: 380px;
    width: 350px;
  }
  .holder__name {
    color: var(--navy);
    font-weight: 700;
    font-size: 29px;
    letter-spacing: 0.5px;
    text-transform: uppercase;
    white-space: nowrap;
  }
  .holder__title {
    color: var(--muted);
    font-size: 22px;
    margin-top: 4px;
  }

  .divider {
    position: absolute;
    left: 452px;
    top: 300px;
    width: 1px;
    height: 130px;
    background: var(--rule);
  }

  .contact {
    position: absolute;
    left: 480px;
    top: 300px;
    list-style: none;
  }
  .contact__item {
    display: flex;
    align-items: center;
    gap: 12px;
    height: 42px;
    color: var(--ink);
    font-size: 21px;
    white-space: nowrap;
  }
  .contact__icon { width: 24px; height: 24px; flex: none; }
</style>
</head>
<body>

  <section class="card card--front" aria-label="Business card front">
    <div class="brand">
      <span class="brand__mark" aria-hidden="true"></span>
      <div class="brand__name">Oak<br>Partners</div>
    </div>

    <div class="holder">
      <div class="holder__name">Dorian Pemberton</div>
      <div class="holder__title">TITLE</div>
    </div>

    <span class="divider" aria-hidden="true"></span>

    <ul class="contact">
      <li class="contact__item">
        <svg class="contact__icon" viewBox="0 0 24 24" aria-hidden="true">
          <path fill="#1b3270" d="M6.6 10.8c1.4 2.8 3.8 5.1 6.6 6.6l2.2-2.2c.3-.3.7-.4 1-.2 1.1.4 2.3.6 3.6.6.6 0 1 .4 1 1V20c0 .6-.4 1-1 1C10.6 21 3 13.4 3 4c0-.6.4-1 1-1h3.5c.6 0 1 .4 1 1 0 1.3.2 2.5.6 3.6.1.3 0 .7-.2 1l-2.3 2.2z"/>
        </svg>
        800-555-0147
      </li>
      <li class="contact__item">
        <svg class="contact__icon" viewBox="0 0 24 24" aria-hidden="true">
          <rect x="2" y="5" width="20" height="14" fill="#1b3270"/>
          <path d="M2 5l10 8 10-8" fill="none" stroke="#fff" stroke-width="1.6"/>
        </svg>
        dorian@oakpartners.example
      </li>
      <li class="contact__item">
        <svg class="contact__icon" viewBox="0 0 24 24" aria-hidden="true">
          <g fill="none" stroke="#1b3270" stroke-width="1.8">
            <circle cx="12" cy="12" r="10"/>
            <ellipse cx="12" cy="12" rx="4.5" ry="10"/>
            <path d="M2 12h20M4 7h16M4 17h16"/>
          </g>
        </svg>
        www.oakpartners.example
      </li>
    </ul>
  </section>

  <section class="card card--back" aria-label="Business card back">
    <div class="brand">
      <span class="brand__mark" aria-hidden="true"></span>
      <div class="brand__name">Oak<br>Partners</div>
    </div>
  </section>

</body>
</html>
```